Southern Plantskills Academy needs a modern website that oozes professionalism

Our current website is boring and looks like everyone elses. We need a modern website that says we are the best at plant operator training. We use Brontovex and Hiraketo equipment for our training. We train all over Australia in Civil Construction, Mining and Quarrying. We want to be the "Go to" website for all plant operator training in Australia.

Industry/Entity Type

Heavy Machinery Training

Colors
0054AA
0677BA
7BADD7
CADEEF
E8F1F8
FFF300
FFF600
FEFA6F
FFFEC7
FFFEE8

```html
<!DOCTYPE html>
<html lang="en">
<head>
<meta charset="utf-8">
<title>Southern Plantskills Academy</title>
<link href="https://fonts.googleapis.com/css2?family=Fira+Sans:wght@500;600;700&family=Open+Sans:wght@400;600;700&display=swap" rel="stylesheet">
<style>
:root{
  --navy:#163a66;
  --navy-dark:#1b3352;
  --blue:#0054aa;
  --blue-mid:#0677ba;
  --sky:#2f9be8;
  --yellow:#f7c31b;
  --yellow-deep:#f2b705;
  --text:#2b4a73;
  --muted:#5b6f8a;
  --pale:#f3f6fa;
  --panel:#edf2f8;
  --white:#ffffff;
}
*{box-sizing:border-box;margin:0;padding:0}
html,body{width:1200px;height:4983px;overflow:hidden}
body{position:relative;background:var(--white);font-family:"Open Sans",sans-serif;color:var(--text)}
.abs{position:absolute}
h1,h2,h3,h4{font-family:"Fira Sans",sans-serif;color:var(--navy);font-weight:600}
.eyebrow{position:absolute;font-size:11px;font-weight:700;letter-spacing:.3px;color:var(--yellow-deep);text-transform:uppercase;display:flex;align-items:center;gap:14px}
.eyebrow::after{content:"";width:50px;height:2px;background:var(--yellow)}
.eyebrow.red::after{background:#b3324a}
.section-title{position:absolute;font-size:46px;line-height:60px;white-space:nowrap}
.btn{position:absolute;background:var(--yellow);color:var(--white);font-family:"Open Sans",sans-serif;font-weight:700;font-size:13px;display:flex;align-items:center;justify-content:center;border-radius:2px}
.arrows{position:absolute;display:flex;gap:8px}
.arrows span{width:45px;height:62px;background:var(--white);box-shadow:0 2px 10px rgba(20,50,90,.15);display:flex;align-items:center;justify-content:center}
.photo{position:absolute}
p{font-size:12.5px;line-height:23px}

.topbar{top:0;left:0;width:1200px;height:35px;background:var(--navy-dark);color:var(--white);font-size:12px;display:flex;align-items:center;justify-content:center;gap:6px}
.brand{display:flex;align-items:center;gap:10px}
.brand-dot{width:40px;height:40px;border-radius:50%;background:var(--navy)}
.brand-name{font-family:"Fira Sans",sans-serif;font-weight:700;font-size:15px;line-height:17px;color:var(--navy);text-transform:uppercase}
.nav{top:108px;left:420px;display:flex;font-size:12px;font-weight:700;color:var(--navy-dark)}
.nav a{text-decoration:none;color:inherit;position:absolute;white-space:nowrap}
.nav a.active{color:var(--blue-mid)}
.nav a.active::after{content:"";position:absolute;left:0;right:0;top:25px;height:2px;background:var(--blue-mid)}

.service-card{position:absolute;top:1055px;width:321px;height:400px;background:var(--white);box-shadow:0 4px 16px rgba(20,50,90,.08);text-align:center}
.service-card .photo{top:0;left:0;width:321px;height:209px}
.service-card .badge{position:absolute;top:172px;left:124px;width:72px;height:72px;border-radius:50%;background:var(--navy);border:4px solid var(--white);display:flex;align-items:center;justify-content:center}
.service-card h3{position:absolute;top:264px;width:100%;font-size:22px}
.service-card p{position:absolute;top:300px;left:30px;right:30px;font-size:12.5px;color:var(--muted)}
.service-card .rule{position:absolute;top:370px;left:141px;width:38px;height:2px;background:var(--yellow)}

.feature{position:absolute;width:260px}
.feature h4{font-size:15px;margin-left:57px}
.feature p{margin-left:57px;font-size:12.5px;color:#4d74a8;margin-top:5px}
.feature svg{position:absolute;left:0;top:0}

.review{position:absolute;top:2910px;width:319px;height:240px;background:var(--panel);border-radius:16px}
.review .quote{position:absolute;top:-21px;left:30px;font-family:"Fira Sans",sans-serif;font-size:80px;line-height:80px;color:var(--yellow);font-weight:700}
.review .stars{position:absolute;top:40px;left:31px;color:var(--yellow);font-size:14px;letter-spacing:2px}
.review h4{position:absolute;top:66px;left:31px;font-size:17px;color:#17253a}
.review p{position:absolute;top:96px;left:31px;right:22px;font-size:12.5px;line-height:24px;color:var(--text)}
.reviewer{position:absolute;top:3196px;display:flex;align-items:center;gap:14px}
.reviewer .avatar{width:40px;height:40px;border-radius:50%;background:#b8a592}
.reviewer b{display:block;font-family:"Fira Sans",sans-serif;color:var(--yellow);font-weight:600;font-size:16px}
.reviewer small{font-size:11px;color:#333}

.field{position:absolute;background:var(--white);border:1px solid #e2e7ee;font-size:11px;color:#8a96a6;padding:0 14px;display:flex;align-items:center}

.footer{top:4528px;left:0;width:1200px;height:455px}
.foot-h{position:absolute;font-family:"Fira Sans",sans-serif;color:var(--white);font-size:15px;font-weight:600;text-transform:uppercase}
.foot-t{position:absolute;color:#dbe4ef;font-size:11.5px;line-height:21px}
.social{position:absolute;width:34px;height:34px;border:1px solid #c9d5e4;display:flex;align-items:center;justify-content:center}
</style>
</head>
<body>

<div class="abs topbar">
  <svg width="12" height="14" viewBox="0 0 12 14"><path d="M6 1a4.5 4.5 0 0 0-4.5 4.5C1.5 9 6 13 6 13s4.5-4 4.5-7.5A4.5 4.5 0 0 0 6 1z" fill="none" stroke="#fff" stroke-width="1.3"/><circle cx="6" cy="5.5" r="1.6" fill="#fff"/></svg>
  <span>48 Quarry Ridge Road, Dubbo NSW</span>
</div>

<header>
  <div class="abs brand" style="top:62px;left:100px">
    <span class="brand-dot"></span>
    <span class="brand-name">Southern Plantskills<br>Academy</span>
  </div>
  <div class="abs" style="top:58px;left:687px;display:flex;align-items:center;gap:10px;font-size:17px;color:var(--navy-dark)">
    <svg width="18" height="18" viewBox="0 0 24 24"><path d="M6.6 10.8a15 15 0 0 0 6.6 6.6l2.2-2.2a1 1 0 0 1 1-.25 11.4 11.4 0 0 0 3.6.57 1 1 0 0 1 1 1V20a1 1 0 0 1-1 1A17 17 0 0 1 3 4a1 1 0 0 1 1-1h3.5a1 1 0 0 1 1 1c0 1.25.2 2.45.57 3.57a1 1 0 0 1-.25 1z" fill="#1b3352"/></svg>
    (02) 5550 1842
  </div>
  <div class="btn" style="top:48px;left:857px;width:190px;height:41px;font-size:11.5px">REQUEST APPOINTMENT</div>
  <nav class="abs nav">
    <a class="active" style="left:2px">HOME</a>
    <a style="left:93px">ABOUT US</a>
    <a style="left:216px">SERVICES</a>
    <a style="left:336px">OUR TEAM</a>
    <a style="left:466px">GALLERY</a>
    <a style="left:584px">CONTACT US</a>
  </nav>
</header>

<section class="abs" style="top:143px;left:0;width:1200px;height:710px">
  <div class="photo" role="img" aria-label="Large yellow mining haul truck driving on a gravel quarry road under a cloudy sky" style="top:0;left:0;width:1200px;height:710px;background:linear-gradient(90deg,#4a6a94 0%,#7d93b0 55%,#a89c80 100%)"></div>
  <svg class="abs" style="top:540px;left:0" width="1200" height="170" viewBox="0 0 1200 170">
    <path d="M0 95 C300 190 800 150 1200 40 L1200 170 L0 170 Z" fill="#f3f6fa"/>
    <path d="M0 95 C300 190 800 150 1200 40" fill="none" stroke="#0054aa" stroke-width="10"/>
    <path d="M0 85 C300 175 800 130 1200 20 L1200 32 C800 145 300 182 0 92 Z" fill="#f7c31b"/>
  </svg>
  <div class="abs" style="top:198px;left:91px;color:#fff;font-size:12.5px;display:flex;align-items:center;gap:22px">Welcome <span style="width:46px;height:1px;background:#fff"></span></div>
  <h1 class="abs" style="top:228px;left:91px;color:#fff;font-size:41px;line-height:59px;white-space:nowrap">Empowering Operators,<br>Fueling Progress</h1>
  <p class="abs" style="top:357px;left:91px;width:430px;color:#eef3f9;font-size:12.5px;line-height:21px">Lorem ipsum dolor sit amet, consectetur adipiscing elit, sed do eiusmod tempor incididunt ut labore et dolore magna Lorem ipsum dolor sit amet, consectetur adipiscing elit, sed do eiusmod tempor incididunt ut labore et dolore magna</p>
  <div class="btn" style="top:470px;left:91px;width:192px;height:41px;font-weight:600">Discover more</div>
</section>

<section class="abs" style="top:853px;left:0;width:1200px;height:695px;background:var(--pale)"></section>
<div class="eyebrow" style="top:926px;left:100px">Our Treatments</div>
<h2 class="section-title" style="top:959px;left:97px">Services We Provide</h2>
<div class="arrows" style="top:944px;left:1010px">
  <span><svg width="10" height="16"><path d="M8 2 2 8l6 6" fill="none" stroke="#1b3352" stroke-width="2"/></svg></span>
  <span><svg width="10" height="16"><path d="M2 2l6 6-6 6" fill="none" stroke="#1b3352" stroke-width="2"/></svg></span>
</div>
<article class="service-card" style="left:93px">
  <div class="photo" role="img" aria-label="Construction worker in hard hat standing in front of an excavator" style="background:linear-gradient(160deg,#a9c3da,#6f7b86)"></div>
  <div class="badge"><svg width="28" height="28" viewBox="0 0 24 24"><path d="M12 3l2.6 5.3 5.9.9-4.3 4.1 1 5.8L12 16.4 6.8 19.1l1-5.8L3.5 9.2l5.9-.9z" fill="none" stroke="#fff" stroke-width="1.5"/></svg></div>
  <h3>Civil Construction</h3>
  <p>Lorem ipsum dolor sit amet, consectetur adi piscing elit sed do eiusmod tmpor</p>
  <div class="rule"></div>
</article>
<article class="service-card" style="left:443px">
  <div class="photo" role="img" aria-label="Mine worker in orange safety vest and hard hat at a rocky site" style="background:linear-gradient(160deg,#ecdcc4,#d59a62)"></div>
  <div class="badge"><svg width="28" height="28" viewBox="0 0 24 24"><path d="M5 20h14M8 20l3-8 3 2 3-6M11 12 8 6" fill="none" stroke="#fff" stroke-width="1.6"/></svg></div>
  <h3>Mining</h3>
  <p>Lorem ipsum dolor sit amet, consectetur adi piscing elit sed do eiusmod tmpor</p>
  <div class="rule"></div>
</article>
<article class="service-card" style="left:790px">
  <div class="photo" role="img" aria-label="Yellow excavator loading sand in a quarry" style="background:linear-gradient(160deg,#dcb27c,#b7844a)"></div>
  <div class="badge"><svg width="28" height="28" viewBox="0 0 24 24"><circle cx="8" cy="8" r="3" fill="none" stroke="#fff" stroke-width="1.5"/><circle cx="16" cy="8" r="3" fill="none" stroke="#fff" stroke-width="1.5"/><path d="M3 19c0-3 2.5-5 5-5s5 2 5 5M11 19c0-3 2.5-5 5-5s5 2 5 5" fill="none" stroke="#fff" stroke-width="1.5"/></svg></div>
  <h3>Quarrying</h3>
  <p>Lorem ipsum dolor sit amet, consectetur adi piscing elit sed do eiusmod tmpor</p>
  <div class="rule"></div>
</article>

<div class="eyebrow" style="top:1632px;left:97px">Treatments</div>
<h2 class="section-title" style="top:1665px;left:95px;line-height:60px">Training Operators<br>for Industry Leaders</h2>
<p class="abs" style="top:1797px;left:97px;width:460px;font-size:12.5px;line-height:24px;color:var(--blue)">Lorem ipsum dolor sit amet, consectetur adipiscing elit, sed do eiusmo empor incididunt ut abore et dolore magna aliqua. Ut enim ad minim iam, quis nostrud exercitation ullamco</p>
<div class="feature" style="top:1902px;left:100px">
  <svg width="42" height="42" viewBox="0 0 24 24"><circle cx="12" cy="12" r="4" fill="none" stroke="#f7c31b" stroke-width="1.2"/><circle cx="12" cy="12" r="8" fill="none" stroke="#f7c31b" stroke-width="1.2" stroke-dasharray="3 2"/></svg>
  <h4>Quality Assurance</h4><p>Lorem ipsum dolor sit amet, consectetur adipiscing</p>
</div>
<div class="feature" style="top:1902px;left:373px">
  <svg width="42" height="42" viewBox="0 0 24 24"><circle cx="11" cy="11" r="7" fill="none" stroke="#f7c31b" stroke-width="1.2"/><circle cx="16" cy="16" r="4" fill="#fff" stroke="#f7c31b" stroke-width="1.2"/></svg>
  <h4>Professional</h4><p>Lorem ipsum dolor sit amet, consectetur adipiscing</p>
</div>
<div class="feature" style="top:1999px;left:100px">
  <svg width="42" height="42" viewBox="0 0 24 24"><circle cx="12" cy="8" r="4" fill="none" stroke="#f7c31b" stroke-width="1.2"/><path d="M4 21c0-4 3.5-7 8-7s8 3 8 7" fill="none" stroke="#f7c31b" stroke-width="1.2"/></svg>
  <h4>Comprehensive Services</h4><p>Lorem ipsum dolor sit amet, consectetur adipiscing</p>
</div>
<div class="feature" style="top:1999px;left:373px">
  <svg width="42" height="42" viewBox="0 0 24 24"><path d="M12 3l2.6 5.3 5.9.9-4.3 4.1 1 5.8L12 16.4 6.8 19.1l1-5.8L3.5 9.2l5.9-.9z" fill="none" stroke="#f7c31b" stroke-width="1.2"/></svg>
  <h4>Client-centric</h4><p>Lorem ipsum dolor sit amet, consectetur adipiscing</p>
</div>
<div class="btn" style="top:2113px;left:104px;width:167px;height:43px">Apply Now</div>
<svg class="abs" style="top:1655px;left:640px" width="475" height="475" viewBox="0 0 475 475">
  <path d="M 60 330 A 225 225 0 1 1 380 420" fill="none" stroke="#163a66" stroke-width="7"/>
</svg>
<div class="photo" role="img" aria-label="Yellow road roller compactor parked in front of green trees" style="top:1683px;left:652px;width:448px;height:448px;border-radius:50%;background:linear-gradient(180deg,#4f7a3a 0%,#c9a43a 100%)"></div>

<section class="abs" style="top:2254px;left:590px;width:610px;height:401px;background:var(--panel)"></section>
<div class="photo" role="img" aria-label="Worker in hard hat and orange vest holding a radio beside a loader" style="top:2233px;left:0;width:590px;height:443px;border:5px solid var(--sky);background:linear-gradient(135deg,#c9d4df,#d99a5a)"></div>
<div class="eyebrow" style="top:2296px;left:648px">About Us</div>
<h2 class="section-title" style="top:2329px;left:646px">Where Training<br>Meets Transformation</h2>
<p class="abs" style="top:2461px;left:648px;width:450px;font-size:12.5px;line-height:24px;color:var(--blue)">Lorem ipsum dolor sit amet, consectetur adipiscing elit, sed do eiusmo empor incididunt ut abore et dolore magna aliqua. Ut enim ad minim iam, quis nostrud exercitation ullamco</p>
<div class="btn" style="top:2568px;left:648px;width:169px;height:44px">Apply Now</div>

<div class="eyebrow" style="top:2764px;left:95px">Testimonials</div>
<h2 class="section-title" style="top:2797px;left:93px">What Clients Are Saying</h2>
<div class="arrows" style="top:2782px;left:1004px">
  <span><svg width="10" height="16"><path d="M8 2 2 8l6 6" fill="none" stroke="#1b3352" stroke-width="2"/></svg></span>
  <span><svg width="10" height="16"><path d="M2 2l6 6-6 6" fill="none" stroke="#1b3352" stroke-width="2"/></svg></span>
</div>
<article class="review" style="left:93px"><div class="quote">“</div><div class="stars">★★★★★</div><h4>They are the Best</h4><p>Lorem ipsum dolor sit amet, consectetur adipiscing elit, sed do eiusmod tempor i ncididunt ut labore et dolore magna aliqua. Ut enim ad minim veniam, quis nostrud exercitation ullamco laboris nisi ut</p></article>
<article class="review" style="left:441px"><div class="quote">“</div><div class="stars">★★★★★</div><h4>They are the Best</h4><p>Lorem ipsum dolor sit amet, consectetur adipiscing elit, sed do eiusmod tempor i ncididunt ut labore et dolore magna aliqua. Ut enim ad minim veniam, quis nostrud exercitation ullamco laboris nisi ut</p></article>
<article class="review" style="left:784px"><div class="quote">“</div><div class="stars">★★★★★</div><h4>They are the Best</h4><p>Lorem ipsum dolor sit amet, consectetur adipiscing elit, sed do eiusmod tempor i ncididunt ut labore et dolore magna aliqua. Ut enim ad minim veniam, quis nostrud exercitation ullamco laboris nisi ut</p></article>
<div class="reviewer" style="left:125px"><span class="avatar" role="img" aria-label="Client portrait"></span><div><b>Jessica</b><small>CEO, Ridgeline Civil</small></div></div>
<div class="reviewer" style="left:472px"><span class="avatar" role="img" aria-label="Client portrait"></span><div><b>Jessica</b><small>CEO, Ridgeline Civil</small></div></div>
<div class="reviewer" style="left:818px"><span class="avatar" role="img" aria-label="Client portrait"></span><div><b>Jessica</b><small>CEO, Ridgeline Civil</small></div></div>

<div class="eyebrow red" style="top:3331px;left:95px">Our Gallery</div>
<h2 class="section-title" style="top:3364px;left:93px">Recent Projects</h2>
<div class="arrows" style="top:3347px;left:1004px">
  <span><svg width="10" height="16"><path d="M8 2 2 8l6 6" fill="none" stroke="#1b3352" stroke-width="2"/></svg></span>
  <span><svg width="10" height="16"><path d="M2 2l6 6-6 6" fill="none" stroke="#1b3352" stroke-width="2"/></svg></span>
</div>
<div class="photo" role="img" aria-label="Muddy earthworks site with apartment buildings behind" style="top:3479px;left:0;width:221px;height:378px;background:linear-gradient(180deg,#8e98a3,#6b5f50)"></div>
<div class="photo" role="img" aria-label="Yellow wheel loader working on a construction site at dusk" style="top:3479px;left:228px;width:740px;height:378px;background:linear-gradient(180deg,#41444b,#55504a)"></div>
<div class="photo" role="img" aria-label="Smiling worker in hard hat and yellow vest with arms crossed" style="top:3479px;left:975px;width:225px;height:378px;background:linear-gradient(180deg,#86a8d2,#7f8a70)"></div>
<h3 class="abs" style="top:3608px;left:228px;width:740px;text-align:center;color:#fff;font-size:37px;line-height:50px;font-weight:700">Painting Project 338<br>in Melbourne</h3>
<p class="abs" style="top:3718px;left:408px;width:380px;text-align:center;color:#e7ebf0;font-size:12px;line-height:20px">Lorem ipsum dolor sit amet, consectetur adipiscing elit, sed do eiusmod tempor incidid</p>
<svg class="abs" style="top:3649px;left:255px" width="36" height="36"><circle cx="18" cy="18" r="17" fill="#fff"/><path d="M23 18H13m4-4-4 4 4 4" fill="none" stroke="#1b3352" stroke-width="1.8"/></svg>
<svg class="abs" style="top:3649px;left:905px" width="36" height="36"><circle cx="18" cy="18" r="17" fill="#fff" fill-opacity=".85"/><path d="M13 18h10m-4-4 4 4-4 4" fill="none" stroke="#1b3352" stroke-width="1.8"/></svg>

<section class="abs" style="top:3922px;left:0;width:1200px;height:606px;background:var(--pale)"></section>
<div class="eyebrow" style="top:3995px;left:135px">Get In Touch</div>
<h2 class="section-title" style="top:4028px;left:132px">Contact Us</h2>
<p class="abs" style="top:4094px;left:137px;font-size:11px;color:var(--muted)">Just send a message, we will answer within 24 hours</p>
<div class="field" style="top:4155px;left:133px;width:198px;height:38px">Your full name</div>
<div class="field" style="top:4155px;left:352px;width:199px;height:38px">Phone Number</div>
<div class="field" style="top:4207px;left:133px;width:198px;height:38px">Mail Address</div>
<div class="field" style="top:4207px;left:352px;width:199px;height:38px">Subject</div>
<div class="field" style="top:4259px;left:133px;width:418px;height:87px;align-items:flex-start;padding-top:12px">Type your message...</div>
<div class="btn" style="top:4369px;left:133px;width:418px;height:35px;font-size:11.5px">Send Your Message</div>
<div class="photo" role="img" aria-label="Two workers in hard hats reviewing a tablet in front of a wheel loader" style="top:4007px;left:608px;width:487px;height:397px;background:linear-gradient(180deg,#c3d3e2,#8e8a74)"></div>

<footer class="abs footer">
  <svg class="abs" style="top:0;left:0" width="1200" height="455" viewBox="0 0 1200 455">
    <rect x="0" y="0" width="1200" height="455" fill="#f3f6fa"/>
    <path d="M0 95 C350 30 850 20 1200 125 L1200 455 L0 455 Z" fill="#1b3352"/>
    <path d="M0 84 C350 10 850 0 1200 100" fill="none" stroke="#0054aa" stroke-width="12"/>
    <path d="M0 95 C350 25 850 15 1200 118" fill="none" stroke="#f7c31b" stroke-width="10"/>
  </svg>
  <div class="abs brand" style="top:138px;left:490px">
    <span class="brand-dot" style="background:#fff"></span>
    <span class="brand-name" style="color:#fff">Southern Plantskills<br>Academy</span>
  </div>
  <div class="foot-h" style="top:188px;left:95px">Contact Us</div>
  <svg class="abs" style="top:232px;left:95px" width="12" height="14" viewBox="0 0 12 14"><path d="M6 1a4.5 4.5 0 0 0-4.5 4.5C1.5 9 6 13 6 13s4.5-4 4.5-7.5A4.5 4.5 0 0 0 6 1z" fill="#fff"/></svg>
  <div class="foot-t" style="top:228px;left:127px;width:190px">Unit 4, 101 Haulage Way, Toowoomba QLD 4350</div>
  <svg class="abs" style="top:290px;left:95px" width="13" height="13" viewBox="0 0 24 24"><path d="M6.6 10.8a15 15 0 0 0 6.6 6.6l2.2-2.2a1 1 0 0 1 1-.25 11.4 11.4 0 0 0 3.6.57 1 1 0 0 1 1 1V20a1 1 0 0 1-1 1A17 17 0 0 1 3 4a1 1 0 0 1 1-1h3.5a1 1 0 0 1 1 1c0 1.25.2 2.45.57 3.57a1 1 0 0 1-.25 1z" fill="#fff"/></svg>
  <div class="foot-t" style="top:285px;left:127px">02 5550 1843</div>
  <svg class="abs" style="top:327px;left:95px" width="14" height="11" viewBox="0 0 14 11"><rect x=".5" y=".5" width="13" height="10" fill="#fff"/><path d="M.5 .5 7 6l6.5-5.5" fill="none" stroke="#1b3352"/></svg>
  <div class="foot-t" style="top:322px;left:127px">train@plantskills-academy.au</div>
  <div class="foot-t" style="top:234px;left:455px;width:290px;text-align:center">Lorem ipsum dolor sit amet, consectetur adipisic ing elit, sed do eiusmod tempor incididunt ut labore et dolore magna aliqua</div>
  <div class="social" style="top:318px;left:538px"><svg width="14" height="14" viewBox="0 0 24 24"><path d="M10 14a5 5 0 0 0 7 0l3-3a5 5 0 0 0-7-7l-1 1M14 10a5 5 0 0 0-7 0l-3 3a5 5 0 0 0 7 7l1-1" fill="none" stroke="#fff" stroke-width="2"/></svg></div>
  <div class="social" style="top:318px;left:583px"><svg width="14" height="14" viewBox="0 0 24 24"><circle cx="18" cy="5" r="3" fill="#fff"/><circle cx="6" cy="12" r="3" fill="#fff"/><circle cx="18" cy="19" r="3" fill="#fff"/><path d="M8.6 10.5l6.8-4M8.6 13.5l6.8 4" stroke="#fff" stroke-width="2"/></svg></div>
  <div class="social" style="top:318px;left:627px"><svg width="14" height="11" viewBox="0 0 14 11"><rect x=".5" y=".5" width="13" height="10" fill="none" stroke="#fff"/><path d="M.5 .5 7 6l6.5-5.5" fill="none" stroke="#fff"/></svg></div>
  <div class="foot-h" style="top:188px;right:93px">Opening Hours</div>
  <div class="foot-t" style="top:233px;right:128px;text-align:right">Mon - Fri: 9am - to - 6pm</div>
  <div class="foot-t" style="top:264px;right:128px;text-align:right">Saturday 9am - to - 2pm</div>
  <div class="foot-t" style="top:295px;right:128px;text-align:right">Sunday : <u>Closed</u></div>
  <svg class="abs" style="top:237px;right:93px" width="15" height="15"><circle cx="7.5" cy="7.5" r="6.5" fill="none" stroke="#fff"/><path d="M7.5 4v4h3" fill="none" stroke="#fff"/></svg>
  <svg class="abs" style="top:268px;right:93px" width="15" height="15"><circle cx="7.5" cy="7.5" r="6.5" fill="none" stroke="#fff"/><path d="M7.5 4v4h3" fill="none" stroke="#fff"/></svg>
  <svg class="abs" style="top:299px;right:93px" width="15" height="15"><circle cx="7.5" cy="7.5" r="6.5" fill="none" stroke="#fff"/><path d="M7.5 4v4h3" fill="none" stroke="#fff"/></svg>
  <div class="abs" style="top:395px;left:40px;width:1120px;height:1px;background:#34506f"></div>
  <div class="foot-t" style="top:404px;left:0;width:1200px;text-align:center;font-size:11px">Southern Plantskills Academy</div>
</footer>

</body>
</html>
```